Storm Restoration Contractor needs a professional letterhead design

Looking for a professional letterhead design. Not looking for your cheapo MS Word standard ones that are readily available. Dont want it to be cookie cutter look like ones readily available online. We just recently changed our logo and want to freshen up all our documents. Our company handles restoring a property back to a pre-loss condition after a storm damages it. For example, wind, hail, flood, fire losses.

Target Market(s)

Property Owners, Homeowners, Property Owners, Commercial Property Owners, Property Management Companies

Industry/Entity Type

Construction Company

Requirements
Must have
• Professional, Use 1 of 2 logo options
• Storm Restoration, Roofing, Siding, Windows

```html
<!DOCTYPE html>
<html lang="en">
<head>
<meta charset="utf-8">
<title>Crestline Exteriors Letterhead</title>
<link href="https://fonts.googleapis.com/css2?family=Open+Sans:wght@400;600;700&display=swap" rel="stylesheet">
<style>
  :root {
    --backdrop: #e6e7e9;
    --paper: #ffffff;
    --brand-blue: #0f75bc;
    --brand-grey: #58595b;
    --on-band: #ffffff;
  }
  * { box-sizing: border-box; margin: 0; padding: 0; }
  html, body {
    width: 1200px; height: 1200px; overflow: hidden;
    background: var(--backdrop);
    font-family: "Open Sans", Arial, sans-serif;
  }
  .letterhead {
    position: absolute;
    left: 194px; top: 40px;
    width: 812px; height: 1120px;
    background: var(--paper);
  }
  .masthead {
    position: absolute;
    top: 43px; left: 0; right: 0;
    display: flex; justify-content: center; align-items: center;
    gap: 12px;
  }
  .masthead-mark {
    width: 84px; height: 84px;
    border-radius: 50%;
    border: 6px solid var(--brand-blue);
  }
  .masthead-divider {
    width: 2px; height: 93px;
    background: var(--brand-blue);
  }
  .company-name {
    color: var(--brand-blue);
    font-weight: 700;
    font-size: 34px;
    line-height: 1.05;
    letter-spacing: 1px;
    text-transform: uppercase;
  }
  .contact-band {
    position: absolute;
    left: 0; right: 0; top: 1067px;
    height: 51px;
    background: var(--brand-blue);
    color: var(--on-band);
  }
  .contact-address {
    position: absolute; top: 5px; left: 0; right: 0;
    text-align: center;
    font-size: 12.5px; font-weight: 600;
  }
  .contact-lines {
    position: absolute; top: 23px; left: 0; right: 0;
    display: flex; justify-content: center; gap: 14px;
    font-size: 14.5px;
  }
  .contact-item { display: flex; align-items: center; gap: 6px; }
  .contact-item svg { width: 11px; height: 11px; fill: var(--on-band); }
  .band-mark {
    position: absolute; right: 4px; top: 1px;
    width: 50px; height: 50px;
    border-radius: 50%;
    border: 4px solid var(--on-band);
  }
</style>
</head>
<body>
  <div class="letterhead">
    <header class="masthead">
      <div class="masthead-mark"></div>
      <div class="masthead-divider"></div>
      <div class="company-name">Crestline<br>Exteriors</div>
    </header>

    <footer class="contact-band">
      <p class="contact-address">4120 N Harbor Lane STE 210, Mesa, AZ 85201</p>
      <div class="contact-lines">
        <span class="contact-item">
          <svg viewBox="0 0 12 12"><path d="M2.5 0.5 4.5 3 3.5 4.3c.8 1.8 2 3 3.8 3.8L8.6 7l2.5 2-1 2.4C5 11 1 7 0.6 1.5z"/></svg>
          555-014-2200
        </span>
        <span class="contact-item">
          <svg viewBox="0 0 12 12"><path d="M0 2h12v8H0z M1 3l5 3.5L11 3" fill="none" stroke="#fff" stroke-width="1.4"/></svg>
          info@crestlinex.com
        </span>
        <span class="contact-item">
          <svg viewBox="0 0 12 12"><path d="M3 0h6v3H3z M0 4h12v5h-2v3H2V9H0z"/><path d="M3.5 8h5v3h-5z" fill="#0f75bc"/></svg>
          555-014-2290
        </span>
        <span class="contact-item">
          <svg viewBox="0 0 12 12"><circle cx="6" cy="6" r="5.2" fill="none" stroke="#fff" stroke-width="1"/><path d="M0.8 6h10.4M6 0.8v10.4M6 0.8c-3 3-3 7.4 0 10.4M6 0.8c3 3 3 7.4 0 10.4" fill="none" stroke="#fff" stroke-width="0.8"/></svg>
          www.crestlinex.com
        </span>
      </div>
      <div class="band-mark"></div>
    </footer>
  </div>
</body>
</html>
```